Website Design for a holiday home letting busines

We require a redesign of our present website www.pinebrookstays.com. We want the website to stand out and look professional and clean to make holiday hunters want to book a caravan or lodge holiday with us. Our logo is red however we DO NOT want the website to be red. We want a natural colour scheme.

The final design should communicate that we are a professional company to book with.

On the home page we require;
Overview of company
Photo
Search box for holiday (check in)
Late Deals
Reviews
News

We would like the following pages designed; home page, available dates page, caravans page, content page.

The website should be responsive for smart phones. One website I do like is http://www.verdoliso.be/nl/

Target Market(s)

Families

Industry/Entity Type

Travel

Number of Pages Required

5+ page

Font styles to use
Serif

Requirements
Must have
• The project must be responsive for mobile phones and tablets.
• Ability to search for holiday home holidays
• We want a natural colour scheme.
Nice to have
• A style we like is http://www.verdoliso.be/nl/
Should not have
• Do not use red as a colour for the website. Our logo is red so this is the only time we want this used.

```html
<!DOCTYPE html>
<html lang="en">
<head>
<meta charset="utf-8">
<title>Pinebrook Stays – Lodge & Caravan Holidays</title>
<link rel="stylesheet" href="https://fonts.googleapis.com/css2?family=Open+Sans:wght@400;600;700;800&display=swap">
<style>
:root{
  --brand:#c8202b;
  --ink:#333333;
  --muted:#777777;
  --nav:#4a4a4a;
  --nav-active:#5e5e5e;
  --dark:#3b3b3b;
  --darker:#2f2f2f;
  --panel:#484848;
  --light:#ececec;
  --white:#ffffff;
  --line:#dddddd;
  --accent:#6f8f5a;
  --sky1:#7fb7d9;
  --sky2:#cfe3d9;
  --sand:#d9c9a3;
}
*{box-sizing:border-box;margin:0;padding:0}
html,body{width:1200px;height:3124px;overflow:hidden}
body{font-family:"Open Sans",Arial,sans-serif;color:var(--ink);background:var(--white);font-size:13px}
.wrap{width:980px;margin:0 auto;position:relative}
.ph{display:block}

/* header */
.site-header{height:120px;background:var(--white)}
.site-header .wrap{height:120px;display:flex;align-items:center;justify-content:space-between}
.brand{display:flex;align-items:center;gap:12px;font-size:30px;font-weight:700;color:var(--brand)}
.brand-mark{width:34px;height:34px;background:var(--brand)}
.contact{display:flex;gap:36px;font-size:14px;color:var(--muted)}
.contact span{display:flex;align-items:center;gap:8px}

/* nav */
.main-nav{height:48px;background:var(--nav)}
.main-nav ul{list-style:none;display:flex;height:48px;width:980px;margin:0 auto}
.main-nav li{color:var(--white);font-size:12px;font-weight:600;padding:0 14px;display:flex;align-items:center;white-space:nowrap}
.main-nav li.active{background:var(--nav-active)}

/* hero */
.hero{height:600px;position:relative;overflow:hidden;background:linear-gradient(180deg,var(--sky1) 0%,var(--sky2) 55%,#8aa66f 75%,var(--sand) 100%)}
.hero-copy{position:absolute;left:110px;top:170px;width:300px;color:var(--white)}
.hero-copy h1{font-size:24px;font-weight:800;line-height:1.25;letter-spacing:.5px}
.hero-copy p{font-size:14px;line-height:1.6;margin:14px 0 22px}
.btn-outline{display:inline-block;border:2px solid var(--white);color:var(--white);font-size:12px;font-weight:700;padding:9px 16px;letter-spacing:.5px}
.frame{position:absolute;border:8px solid var(--white);box-shadow:0 4px 14px rgba(0,0,0,.3)}
.frame-family{left:580px;top:40px;width:420px;height:440px;transform:rotate(-3deg);background:linear-gradient(160deg,#8fc0dd,#e7d2b8 60%,#c9a27f)}
.frame-caravan{left:490px;top:300px;width:200px;height:170px;transform:rotate(-6deg);background:linear-gradient(180deg,#b9d3e4,#d8d2bf 60%,#8ea56e)}
.frame-lodge{left:930px;top:260px;width:190px;height:200px;transform:rotate(4deg);background:linear-gradient(180deg,#a9cbe0,#e4dccb 60%,#93a978)}
.dots{position:absolute;left:0;right:0;bottom:28px;display:flex;justify-content:center;gap:10px}
.dots i{width:11px;height:11px;border-radius:50%;background:rgba(255,255,255,.55)}
.dots i.on{background:var(--white)}

/* intro band */
.intro{height:392px;background:var(--dark);color:#e5e5e5}
.intro .wrap{display:flex;gap:32px;padding-top:40px}
.intro-col{width:260px}
.intro-col h2,.search h2{font-size:15px;font-weight:700;color:var(--white);letter-spacing:.5px;margin-bottom:16px;display:flex;justify-content:space-between}
.arrows{color:#aaa;font-size:15px;letter-spacing:6px}
.intro-photo{height:160px}
.intro-col p{font-size:11px;line-height:1.6;margin-top:14px;color:#cfcfcf}
.search{width:388px;margin-left:8px}
.search h2{font-size:30px;font-weight:700;margin:4px 0 0}
.search .sub{font-size:15px;color:#cfcfcf;margin-bottom:26px;letter-spacing:.5px}
.field{height:40px;background:var(--panel);margin-bottom:12px;display:flex;align-items:center;justify-content:space-between;padding:0 14px;color:#d5d5d5;font-size:13px}
.btn-search{display:inline-block;background:#555;color:var(--white);font-weight:700;padding:12px 28px;font-size:13px;letter-spacing:.5px;margin-top:4px}

/* listings */
.section-title{font-size:16px;font-weight:800;letter-spacing:.5px;display:flex;justify-content:space-between;align-items:center;margin-bottom:28px}
.section-title .arrows{color:#999}
.cards{display:flex;gap:40px}
.card{width:300px;background:var(--white)}
.card-photo{height:180px}
.card-body{padding:16px 14px}
.card-body h3{font-size:13px;font-weight:800;letter-spacing:.3px;margin-bottom:8px}
.card-body .meta{font-size:11px;color:var(--muted);line-height:1.6}
.card-body .more{text-align:right;font-size:11px;font-weight:700;margin-top:12px;color:var(--ink)}
.caravans{height:480px;background:var(--light);padding-top:48px}
.deals{height:600px;background:var(--white);padding-top:48px}
.deals .card-photo{height:205px}
.deals .card-body{padding:16px 0}
.deals .date{font-size:12px;color:var(--ink);margin-bottom:6px}
.btn-book{display:inline-block;background:var(--darker);color:var(--white);font-size:11px;font-weight:700;padding:11px 18px;margin-top:16px;letter-spacing:.3px}

/* community */
.community{height:620px;background:var(--light);padding-top:40px}
.box{width:300px;height:540px;background:var(--white);padding:22px 18px;overflow:hidden}
.box h3{font-size:13px;font-weight:800;letter-spacing:.4px;margin-bottom:18px}
.review{margin-bottom:22px}
.review b{display:block;font-size:12px}
.review em{display:block;font-style:normal;font-size:11px;color:var(--accent);margin:2px 0 6px}
.review p,.post p{font-size:11px;line-height:1.6;color:var(--muted)}
.post{display:flex;gap:12px;margin-bottom:22px}
.post .thumb{width:60px;height:60px;flex:none;background:linear-gradient(160deg,#c8b59a,#8d9f7c)}
.post b{display:block;font-size:12px;margin-bottom:4px}
.feed{padding:0}
.feed-head{height:36px;background:#5b6d55;color:var(--white);font-size:12px;font-weight:700;display:flex;align-items:center;padding:0 14px}
.feed-item{display:flex;gap:10px;padding:12px 14px;border-bottom:1px solid var(--line)}
.feed-item .thumb{width:40px;height:40px;flex:none;background:linear-gradient(160deg,#cdd8c4,#9cb08a)}
.feed-item p{font-size:11px;line-height:1.5;color:var(--ink)}
.feed-item small{display:block;font-size:10px;color:var(--muted);margin-top:3px}
.feed-foot{padding:12px 14px;font-size:11px;color:var(--muted)}

/* footer */
.site-footer{height:264px;background:var(--darker);color:#cfcfcf;padding-top:30px;overflow:hidden}
.footer-cols{display:flex;gap:60px;height:150px}
.footer-cols ul{list-style:none;width:200px}
.footer-cols li{font-size:12px;line-height:22px}
.footer-right{margin-left:auto;display:flex;flex-direction:column;align-items:center;gap:12px}
.badge{width:96px;height:96px;border-radius:50%;background:#4f7a3a;border:5px solid #e8e8e8}
.btn-chat{background:#555;color:var(--white);font-size:12px;font-weight:700;padding:9px 26px;letter-spacing:.5px}
.footer-bottom{display:flex;justify-content:space-between;align-items:center;margin-top:22px;font-size:11px;border-top:1px solid #444;padding-top:14px;line-height:16px}
.follow{display:flex;align-items:center;gap:10px}
.follow i{width:16px;height:16px;border-radius:50%;background:#888;display:inline-block}
</style>
</head>
<body>

<header class="site-header">
  <div class="wrap">
    <div class="brand"><span class="brand-mark"></span>Pinebrook Stays</div>
    <div class="contact">
      <span><svg width="14" height="14" viewBox="0 0 24 24"><path d="M6.6 10.8a15 15 0 0 0 6.6 6.6l2.2-2.2c.3-.3.7-.4 1-.2 1.1.4 2.3.6 3.6.6.6 0 1 .4 1 1V20c0 .6-.4 1-1 1A17 17 0 0 1 3 4c0-.6.4-1 1-1h3.5c.6 0 1 .4 1 1 0 1.2.2 2.4.6 3.6.1.3 0 .7-.2 1z" fill="#888"/></svg>01632 960 418</span>
      <span><svg width="16" height="12" viewBox="0 0 16 12"><rect x=".5" y=".5" width="15" height="11" fill="none" stroke="#888"/><path d="M.5 .5 8 7l7.5-6.5" fill="none" stroke="#888"/></svg>info@pinebrookstays.com</span>
    </div>
  </div>
</header>

<nav class="main-nav">
  <ul>
    <li class="active">Home</li><li>News</li><li>Reviews</li><li>Caravans &amp; Lodges</li><li>2015 Holidays</li><li>2016 Holidays</li><li>Payment Plans</li><li>Ashcombe Bay</li><li>Local Attractions</li>
  </ul>
</nav>

<section class="hero">
  <div class="hero-copy">
    <h1>PRIVATE HOLIDAY RENTALS</h1>
    <p>Quality Lodge &amp; Caravan hire at Ashcombe Bay Holiday Park. Book online today!</p>
    <span class="btn-outline">MORE DETAILS</span>
  </div>
  <div class="frame frame-caravan" role="img" aria-label="Photo of a static caravan on the holiday park"></div>
  <div class="frame frame-family" role="img" aria-label="Photo of a smiling family outside their holiday lodge"></div>
  <div class="frame frame-lodge" role="img" aria-label="Photo of a holiday lodge exterior"></div>
  <div class="dots"><i class="on"></i><i></i><i></i><i></i><i></i></div>
</section>

<section class="intro">
  <div class="wrap">
    <div class="intro-col">
      <h2>ABOUT US</h2>
      <div class="intro-photo ph" role="img" aria-label="Photo of a holiday homes sign at the park entrance" style="background:linear-gradient(160deg,#dfe6e0,#a9b79b)"></div>
      <p>We have flexible low cost weekly and monthly payment plans available, book from as little as £5 per week to secure your break with us.</p>
    </div>
    <div class="intro-col">
      <h2>GALLERY <span class="arrows">‹ ›</span></h2>
      <div class="intro-photo ph" role="img" aria-label="Photo of a caravan lounge interior" style="background:linear-gradient(160deg,#e2d6c2,#a98d6c)"></div>
      <p>The Alder Caravan</p>
    </div>
    <div class="search">
      <h2>SEARCH BOX</h2>
      <div class="sub">FOR HOLIDAY</div>
      <div class="field">Check in <svg width="14" height="14" viewBox="0 0 14 14"><rect x="1" y="2" width="12" height="11" fill="none" stroke="#bbb"/><path d="M1 5h12M4 0v3M10 0v3" stroke="#bbb"/></svg></div>
      <div class="field">Number of Nights <svg width="14" height="14" viewBox="0 0 14 14"><rect x="1" y="2" width="12" height="11" fill="none" stroke="#bbb"/><path d="M1 5h12M4 0v3M10 0v3" stroke="#bbb"/></svg></div>
      <span class="btn-search">SEARCH</span>
    </div>
  </div>
</section>

<section class="caravans">
  <div class="wrap">
    <div class="section-title">OUR CARAVANS AND LODGES <span class="arrows">‹ ›</span></div>
    <div class="cards">
      <article class="card">
        <div class="card-photo ph" role="img" aria-label="Photo of the Heron Lodge living room" style="background:linear-gradient(160deg,#eae0cf,#a58b6d)"></div>
        <div class="card-body"><h3>HERON LODGE</h3><div class="meta">Lodge | Grade Luxury Lodge | 8 Sleeps<br>| 3 Bedroom</div><div class="more">MORE DETAILS</div></div>
      </article>
      <article class="card">
        <div class="card-photo ph" role="img" aria-label="Photo of the Willow caravan lounge" style="background:linear-gradient(160deg,#efe4d3,#b49877)"></div>
        <div class="card-body"><h3>THE WILLOW CARAVAN</h3><div class="meta">Lodge | Grade Luxury Lodge | 8 Sleeps<br>| 3 Bedroom</div><div class="more">MORE DETAILS</div></div>
      </article>
      <article class="card">
        <div class="card-photo ph" role="img" aria-label="Photo of the Willow II caravan lounge" style="background:linear-gradient(160deg,#e7ddd0,#9c8166)"></div>
        <div class="card-body"><h3>THE WILLOW II CARAVAN</h3><div class="meta">Lodge | Grade Luxury Lodge | 8 Sleeps<br>| 3 Bedroom</div><div class="more">MORE DETAILS</div></div>
      </article>
    </div>
  </div>
</section>

<section class="deals">
  <div class="wrap">
    <div class="section-title">LATE DEALS</div>
    <div class="cards">
      <article class="card">
        <div class="card-photo ph" role="img" aria-label="Photo of the Linnet caravan lounge" style="background:linear-gradient(160deg,#e6d7c2,#a88a67)"></div>
        <div class="card-body"><h3>THE LINNET</h3><div class="date">Friday 04 September 2015 (3 nights)</div><div class="meta">Lodge | Grade Luxury Lodge | 8 Sleeps<br>| 3 Bedroom</div><span class="btn-book">BOOK NOW FOR £149.00</span></div>
      </article>
      <article class="card">
        <div class="card-photo ph" role="img" aria-label="Photo of the Kestrel caravan interior" style="background:linear-gradient(160deg,#ede6dc,#b9a48b)"></div>
        <div class="card-body"><h3>THE KESTREL</h3><div class="date">Friday 04 September 2015 (3 nights)</div><div class="meta">Lodge | Grade Luxury Lodge | 8 Sleeps<br>| 3 Bedroom</div><span class="btn-book">BOOK NOW FOR £149.00</span></div>
      </article>
      <article class="card">
        <div class="card-photo ph" role="img" aria-label="Photo of the Linnet caravan kitchen" style="background:linear-gradient(160deg,#e2d9cc,#8e7a63)"></div>
        <div class="card-body"><h3>THE LINNET</h3><div class="date">Friday 04 September 2015 (3 nights)</div><div class="meta">Lodge | Grade Luxury Lodge | 8 Sleeps<br>| 3 Bedroom</div><span class="btn-book">BOOK NOW FOR £149.00</span></div>
      </article>
    </div>
  </div>
</section>

<section class="community">
  <div class="wrap cards">
    <div class="box">
      <h3>LATEST REVIEWS</h3>
      <div class="review"><b>Marian Holt</b><em>Stayed in Heron Lodge</em><p>Very clean on arrival. Nice quiet location with fantastic views over the bay. We all had an amazing time.</p></div>
      <div class="review"><b>Tessa Kowal</b><em>Stayed in The Linnet</em><p>Very enjoyable, brilliant location and site. Great location near the fireworks and the pool.</p></div>
      <div class="review"><b>Alice Warden</b><em>Stayed in The Linnet</em><p>Had a great stay, would definitely recommend. Very clean and comfortable accommodation.</p></div>
    </div>
    <div class="box">
      <h3>OUR BLOG</h3>
      <div class="post"><div class="thumb" role="img" aria-label="Thumbnail of a live stage show"></div><div><b>Easter With Owen Marsh</b><p>Owen Marsh is coming to Ashcombe Bay for an Easter show on Saturday 4th April.</p></div></div>
      <div class="post"><div class="thumb" role="img" aria-label="Thumbnail of the park swimming pool"></div><div><b>Heatwave To Return</b><p>The sun is back this week, so pack your swimwear and enjoy the outdoor pool.</p></div></div>
      <div class="post"><div class="thumb" role="img" aria-label="Thumbnail of the park restaurant"></div><div><b>New Evening Show</b><p>The park entertainment team have a new evening show planned for the season.</p></div></div>
    </div>
    <div class="box feed">
      <div class="feed-head">Recent Activity</div>
      <div class="feed-item"><div class="thumb"></div><div><p>Booking for summer week now open at the park.</p><small>2 people like this</small></div></div>
      <div class="feed-item"><div class="thumb"></div><div><p>It is a long established fact that a family break by the sea works wonders.</p><small>1 person likes this</small></div></div>
      <div class="feed-item"><div class="thumb"></div><div><p>There are many varieties of lodges on offer this year.</p><small>3 people like this</small></div></div>
      <div class="feed-item"><div class="thumb"></div><div><p>The standard views of the bay are stunning.</p><small>5 people like this</small></div></div>
      <div class="feed-foot">Social feed plugin</div>
    </div>
  </div>
</section>

<footer class="site-footer">
  <div class="wrap">
    <div class="footer-cols">
      <ul><li>About us</li><li>News</li><li>Caravans &amp; Lodges</li><li>2015 Holidays</li><li>2016 Holidays</li><li>Late Deals</li></ul>
      <ul><li>Ashcombe Bay</li><li>Local Attractions</li><li>Little Explorers Club</li><li>Contact Us</li><li>Reviews</li><li>Family Activities</li></ul>
      <ul><li>Frequently Asked Questions</li><li>Park Entertainment Passes</li><li>Privacy Policy</li><li>Booking Terms</li></ul>
      <div class="footer-right">
        <div class="badge" role="img" aria-label="Review rating badge"></div>
        <span class="btn-chat">LIVE CHAT</span>
      </div>
    </div>
    <div class="footer-bottom">
      <div class="follow">Follow us on <i></i><i></i></div>
      <div>Copyright © 2015 All Rights Reserved</div>
    </div>
  </div>
</footer>

</body>
</html>
```